Varentoria Business Card and Letter Head

We are a leadership assessment consultancy based in Sydney, Australia. We help executive-level decison-makers select leaders for more senior level roles in corporate and government organisations. Our methodology is based on the latest research from the field of neuroscience.
We need a business card design and matching letter head that presents our company, Varentoria, as a:
1. trusted adviser to senior executive-level decison makers
2. niche consultancy who are experts in the field of assessing leadership talent
3. results-focused solution provider who balance scientific methods with pragmatic solutions
The following company details should be used in all designs:
Company Name: Varentoria
Details (for business card):
Derek Hanford
Prime Capacity Officer
Level 29, Marlow Tower
7 Marlow Square
Sydney, NSW 2000 Australia
Phone: 1300 582 714
Mobile: 0412 637 258
Email: derek.hanford@varentoria-example.com.au
Website: varentoria-example.com.au
I have attached the logo for Varentoria (for both a white and black background) - your business card and letter head designs must incoporate this logo and colour scheme.
Thanks for your interest in this project, I'm looking forward to receiving your ideas.
Regards,
Derek
Target Market(s)
Executive-level decison-makers in corporate and government organisations (e.g., CEO, VP, Head of Human Resources)
Industry/Entity Type
Leadership
Look and feel

```html
<!DOCTYPE html>
<html lang="en">
<head>
<meta charset="utf-8">
<title>Varentoria Stationery</title>
<link rel="stylesheet" href="https://fonts.googleapis.com/css2?family=Arimo:wght@400;700&family=Quicksand:wght@400;500&family=Roboto+Condensed:wght@400&display=swap">
<style>
:root{
  --bg:#ece4da;
  --paper:#ffffff;
  --charcoal:#3f3f41;
  --charcoal-deep:#333335;
  --mid-grey:#9a9a9c;
  --light-grey:#c9c9cb;
  --red:#c8281d;
  --text:#2b2b2b;
}
*{margin:0;padding:0;box-sizing:border-box}
html,body{width:1200px;height:834px;overflow:hidden;background:var(--bg)}
body{position:relative;font-family:"Arimo",Arial,sans-serif;color:var(--text)}
.sheet{position:absolute;background:var(--paper);box-shadow:0 2px 6px rgba(0,0,0,.25)}
.dark-radial{background:radial-gradient(ellipse at 50% 45%,#b9b9bb 0%,#7a7a7c 40%,var(--charcoal) 75%)}
.brand{display:flex;align-items:center;gap:6px;font-family:"Arimo",Arial,sans-serif;font-weight:700;color:var(--charcoal);white-space:nowrap}
.brand-square{width:12px;height:12px;background:var(--red)}
.address{font-family:"Roboto Condensed",Arial,sans-serif;font-size:7.5px;line-height:11px;color:var(--text)}
.divider{width:1px;background:#bdbdbd}
.web{font-family:"Quicksand",Arial,sans-serif;font-weight:500;letter-spacing:.4px}
.footer-rule{position:absolute;height:3px;background:linear-gradient(90deg,transparent,#d2d2d2 15%,#d2d2d2 85%,transparent)}

/* letterhead */
.letterhead{left:27px;top:41px;width:530px;height:750px}
.letterhead .topbar{height:26px;background:linear-gradient(90deg,var(--charcoal-deep),#9d9d9f 60%,var(--charcoal-deep))}
.letterhead .head{position:absolute;left:110px;top:40px;display:flex;gap:18px;align-items:center}
.letterhead .brand{font-size:20px}
.letterhead .divider{height:38px}
.letterhead .footer-rule{left:20px;right:20px;top:718px}
.letterhead .web{position:absolute;left:0;right:0;top:730px;text-align:center;color:var(--red);font-size:11.5px}

/* card back */
.card-back{left:106px;top:225px;width:293px;height:162px;display:flex;align-items:center;justify-content:center}
.card-back .brand{color:rgba(255,255,255,.75);font-size:22px}

/* card front */
.card-front{left:201px;top:416px;width:295px;height:164px;display:flex;overflow:hidden}
.card-front .face{width:145px;display:flex;flex-direction:column;justify-content:center;padding-left:12px}
.card-front .brand{font-size:15px}
.card-front .brand-square{width:9px;height:9px}
.card-front .web{font-size:9px;color:#555;margin-top:20px}
.card-front .details{flex:1;background:radial-gradient(ellipse at 55% 60%,#9d9d9f 0%,#646466 45%,var(--charcoal) 80%);padding:20px 0 0 8px;color:#fff}
.card-front .name{font-weight:700;color:var(--red);font-size:14px}
.card-front .role{font-family:"Quicksand",Arial,sans-serif;font-size:9.5px;margin-top:2px}
.card-front ul{list-style:none;margin-top:9px}
.card-front li{display:flex;gap:6px;font-family:"Roboto Condensed",Arial,sans-serif;font-size:7px;line-height:11.5px}
.card-front li svg{flex:none;margin-top:2px}
.card-front li.addr{margin-top:5px}

/* envelope */
.envelope{position:absolute;left:578px;top:60px;width:600px;height:374px}
.envelope .body{position:absolute;left:0;top:111px;width:600px;height:263px;background:var(--paper);box-shadow:0 2px 6px rgba(0,0,0,.25)}
.envelope .flap-mark{position:absolute;left:0;right:0;top:40px;text-align:center}
.envelope .flap-mark .brand{display:inline-flex;color:rgba(255,255,255,.45);font-size:18px}
.envelope .head{position:absolute;left:26px;top:40px;display:flex;gap:14px;align-items:center}
.envelope .brand{font-size:18px}
.envelope .divider{height:34px}
.envelope .address{font-size:7px;line-height:10px}
.envelope .footer-rule{left:10px;right:10px;top:228px}
.envelope .web{position:absolute;left:0;right:0;top:240px;text-align:center;color:var(--red);font-size:10.5px}

/* disc */
.disc{position:absolute;left:876px;top:476px}

/* cover */
.cover{left:602px;top:474px;width:305px;height:315px}
.cover .panel{height:157px;display:flex;align-items:center;justify-content:center;background:radial-gradient(ellipse at 50% 40%,#b9b9bb 0%,#7f7f81 45%,var(--charcoal) 80%)}
.cover .panel .brand{color:#eaeaea;font-weight:700;font-size:24px}
.cover .title{text-align:center;margin-top:24px;font-family:"Quicksand",Arial,sans-serif;font-size:17px;color:var(--red);letter-spacing:.5px}
.cover .footer-rule{left:4px;right:4px;top:290px}
.cover .web{position:absolute;left:0;right:0;top:298px;text-align:center;font-size:10px;color:#333}
</style>
</head>
<body>

<section class="sheet letterhead" aria-label="Letterhead">
  <div class="topbar"></div>
  <header class="head">
    <div class="brand"><span class="brand-square"></span>Varentoria</div>
    <div class="divider"></div>
    <p class="address">Level 29, Marlow Tower, 7 Marlow Square,<br>Sydney NSW 2000 Australia<br>Phone: 1300 582 714&nbsp;&nbsp;Mobile: 0412 637 258</p>
  </header>
  <div class="footer-rule"></div>
  <p class="web">www.varentoria-example.com.au</p>
</section>

<section class="sheet card-back dark-radial" aria-label="Business card back">
  <div class="brand">Varentoria</div>
</section>

<section class="sheet card-front" aria-label="Business card front">
  <div class="face">
    <div class="brand"><span class="brand-square"></span>Varentoria</div>
    <p class="web">www.varentoria-example.com.au</p>
  </div>
  <div class="details">
    <p class="name">Derek Hanford</p>
    <p class="role">Prime Capacity Officer</p>
    <ul>
      <li><svg width="6" height="7" viewBox="0 0 6 7"><path d="M1 0h1.5l.5 2-1 .7a4 4 0 0 0 1.6 1.8l.8-.9 1.6.6V6a1 1 0 0 1-1 1C2.5 7 0 4.5 0 1a1 1 0 0 1 1-1z" fill="#fff"/></svg>1300 582 714</li>
      <li><svg width="6" height="7" viewBox="0 0 6 7"><rect x=".5" y=".5" width="4" height="6" rx=".8" fill="none" stroke="#fff"/></svg>0412 637 258</li>
      <li><svg width="7" height="6" viewBox="0 0 7 6"><rect x=".5" y=".5" width="6" height="4.5" fill="none" stroke="#fff"/><path d="M.5.5 3.5 3l3-2.5" fill="none" stroke="#fff"/></svg>derek.hanford@varentoria-example.com.au</li>
      <li class="addr"><svg width="6" height="8" viewBox="0 0 6 8"><rect x=".5" y=".5" width="5" height="7" fill="none" stroke="#fff"/><path d="M2 2h2M2 4h2M2 6h2" stroke="#fff"/></svg><span>Level 29, Marlow Tower<br>7 Marlow Square<br>Sydney, NSW 2000 Australia</span></li>
    </ul>
  </div>
</section>

<section class="envelope" aria-label="Envelope">
  <svg width="600" height="114" viewBox="0 0 600 114" style="position:absolute;left:0;top:0">
    <defs>
      <linearGradient id="flapShade" x1="0" x2="1">
        <stop offset="0" stop-color="#3a3a3c"/><stop offset=".5" stop-color="#a3a3a5"/><stop offset="1" stop-color="#3a3a3c"/>
      </linearGradient>
    </defs>
    <path d="M0 111 L18 66 Q24 54 40 50 L270 6 Q300 0 330 6 L560 50 Q576 54 582 66 L600 111 Z" fill="url(#flapShade)"/>
  </svg>
  <div class="flap-mark"><span class="brand">Varentoria</span></div>
  <div class="body">
    <header class="head">
      <div class="brand"><span class="brand-square"></span>Varentoria</div>
      <div class="divider"></div>
      <p class="address">Level 29, Marlow Tower, 7 Marlow Square,<br>Sydney NSW 2000 Australia<br>Phone: 1300 582 714&nbsp;&nbsp;Mobile: 0412 637 258</p>
    </header>
    <div class="footer-rule"></div>
    <p class="web">www.varentoria-example.com.au</p>
  </div>
</section>

<svg class="disc" width="320" height="320" viewBox="0 0 320 320" aria-label="Disc label">
  <defs>
    <radialGradient id="discShade" cx=".5" cy=".3" r=".6">
      <stop offset="0" stop-color="#a8a8aa"/><stop offset=".6" stop-color="#6b6b6d"/><stop offset="1" stop-color="#3f3f41"/>
    </radialGradient>
    <clipPath id="discClip"><circle cx="157" cy="157" r="150"/></clipPath>
    <mask id="discHole"><rect width="320" height="320" fill="#fff"/><circle cx="157" cy="157" r="30" fill="#000"/></mask>
  </defs>
  <g mask="url(#discHole)">
    <circle cx="157" cy="157" r="157" fill="#dcdcdc"/>
    <circle cx="157" cy="157" r="152" fill="#fff"/>
    <g clip-path="url(#discClip)">
      <path d="M0 0H320V230L0 90Z" fill="url(#discShade)"/>
    </g>
    <circle cx="157" cy="157" r="144" fill="none" stroke="#fff" stroke-width="1"/>
    <text x="200" y="100" text-anchor="middle" font-family="Arimo, Arial, sans-serif" font-weight="700" font-size="16" fill="rgba(255,255,255,.7)">Varentoria</text>
    <text font-family="Quicksand, Arial, sans-serif" font-size="18" fill="#c8281d" transform="translate(118 180) rotate(27)">Your Title Here</text>
    <text font-family="Quicksand, Arial, sans-serif" font-weight="500" font-size="10" fill="#333" transform="translate(104 238) rotate(20)">www.varentoria-example.com.au</text>
  </g>
</svg>

<section class="sheet cover" aria-label="Disc cover">
  <div class="panel"><div class="brand">Varentoria</div></div>
  <p class="title">Your Title Here</p>
  <div class="footer-rule"></div>
  <p class="web">www.varentoria-example.com.au</p>
</section>

</body>
</html>
```